Clendora Hand Sanitizer One Page Website

I need someone to make a one page website for us. The site is www.clendora-example.com. I quickly created a simple basic page with all the elements (text, picture, table of pricing, pdf links) needed. I need someone to make the webpage look nice, professioonal, and responsive. There are only 2 links on the page pointing to two pdf files, otherwise there is no navigation needed. The product is a hand sanitizer.
Target Market(s)
Government, corporations, hospitals, large companies
Number of Pages Required
1 page
Requirements
Nice to have
- A hero image relating to hand sanitizer products would be really nice
We would like the bulleted items (Active Ingredient 75% Isopropyl Alcohol, etc) to somehow incorporate icons like the attached picture.

```html
<!DOCTYPE html>
<html lang="en">
<head>
<meta charset="utf-8">
<title>Clendora Hand Sanitizer</title>
<link href="https://fonts.googleapis.com/css2?family=Quicksand:wght@700&family=Open+Sans:wght@400&family=Roboto:wght@400;500&display=swap" rel="stylesheet">
<style>
:root{
  --blue:#1a93cc;
  --ink:#333;
  --text:#222;
  --muted:#555;
  --head:#444444;
  --row-alt:#f6f6f6;
  --line:#cfcfcf;
  --footer:#eeeeee;
  --hero-a:#eef1f3;
  --hero-b:#dde5ea;
  --hero-c:#e9ddd2;
  --product-a:#dfe3e8;
  --product-b:#c4ccd6;
}
*{margin:0;padding:0;box-sizing:border-box}
html,body{width:1065px;height:1200px;overflow:hidden;background:#fff}
body{position:relative;font-family:'Roboto',sans-serif;color:var(--text)}
.hero{position:absolute;left:0;top:0;width:1065px;height:675px}
.hero-photo{position:absolute;inset:0;background:linear-gradient(100deg,var(--hero-a) 0%,var(--hero-b) 55%,var(--hero-c) 100%)}
.logo{position:absolute;left:101px;top:36px;display:flex;align-items:center;gap:12px}
.logo-dot{width:38px;height:38px;border-radius:50%;background:var(--blue)}
.logo-name{font-family:'Roboto',sans-serif;font-weight:400;font-size:40px;line-height:44px;color:var(--ink);letter-spacing:1px}
.headline{position:absolute;left:104px;top:222px;font-family:'Quicksand',sans-serif;font-weight:700;font-size:33px;line-height:44px;color:var(--ink)}
.headline .accent{color:var(--blue)}
.features{position:absolute;left:104px;top:368px;list-style:none;font-family:'Open Sans',sans-serif;font-size:13.5px;line-height:20.5px;color:var(--text);width:380px}
.features li{display:flex;gap:9px;margin-bottom:13px}
.features li.wide{width:420px}
.features svg{flex:none;margin-top:3px}
.nav-arrow{position:absolute;top:335px}
.nav-prev{left:40px}.nav-next{left:1024px}
.pricing{position:absolute;left:104px;top:740px;width:619px;border-collapse:collapse;font-size:13.5px;color:var(--muted);box-shadow:0 2px 6px rgba(0,0,0,.08)}
.pricing th{background:var(--head);color:#fff;font-weight:500;text-align:left;height:58px;padding:0 0 0 16px;line-height:15px;vertical-align:middle}
.pricing td{height:43px;padding:0 0 0 17px;font-weight:400}
.pricing tbody tr:nth-child(even){background:var(--row-alt)}
.pricing th+th,.pricing td+td{border-left:1px solid var(--line)}
.pricing th.nosep,.pricing td.nosep{border-left:none}
.pricing th:first-child,.pricing td:first-child{padding-left:29px}
.stock{position:absolute;left:101px;top:1011px;font-size:17px;line-height:23px;color:var(--muted)}
.stock p+p{margin-top:9px}
.doc-link{position:absolute;top:1021px;width:173px;height:41px;border:2px solid var(--blue);color:var(--blue);font-weight:500;font-size:13.5px;display:flex;align-items:center;justify-content:center;gap:6px;text-decoration:none}
.doc-compliance{left:340px}
.doc-sds{left:526px}
.product-photo{position:absolute;left:740px;top:695px;width:300px;height:400px;border-radius:6px;background:linear-gradient(180deg,var(--product-a) 0%,var(--product-b) 100%)}
.footer{position:absolute;left:0;top:1136px;width:1065px;height:64px;background:var(--footer);text-align:center;line-height:64px;font-size:13px;color:var(--muted)}
</style>
</head>
<body>
<header class="hero">
  <div class="hero-photo" role="img" aria-label="Photo of a woman applying hand sanitizer to a child's hand"></div>
  <div class="logo"><span class="logo-dot"></span><span class="logo-name">LINEREADY</span></div>
  <h1 class="headline">Isopropyl Alcohol Antiseptic<br>75% Topical Solution<br><span class="accent">Hand Sanitizer</span></h1>
  <ul class="features">
    <li><svg width="15" height="15" viewBox="0 0 16 16"><circle cx="8" cy="8" r="7" fill="none" stroke="#1a93cc" stroke-width="1.4"/><path d="M4.6 8.2l2.3 2.2 4.4-4.6" fill="none" stroke="#1a93cc" stroke-width="1.6"/></svg><span>Active Ingredient 75% Isopropyl Alcohol</span></li>
    <li><svg width="15" height="15" viewBox="0 0 16 16"><circle cx="8" cy="8" r="7" fill="none" stroke="#1a93cc" stroke-width="1.4"/><path d="M4.6 8.2l2.3 2.2 4.4-4.6" fill="none" stroke="#1a93cc" stroke-width="1.6"/></svg><span>USDA rated E3 hand sanitizer, FDA drug registration number (54555-126)</span></li>
    <li><svg width="15" height="15" viewBox="0 0 16 16"><circle cx="8" cy="8" r="7" fill="none" stroke="#1a93cc" stroke-width="1.4"/><path d="M4.6 8.2l2.3 2.2 4.4-4.6" fill="none" stroke="#1a93cc" stroke-width="1.6"/></svg><span>Meets World Health Organization (WHO) guidelines for an effective hand sanitizer</span></li>
    <li><svg width="15" height="15" viewBox="0 0 16 16"><circle cx="8" cy="8" r="7" fill="none" stroke="#1a93cc" stroke-width="1.4"/><path d="M4.6 8.2l2.3 2.2 4.4-4.6" fill="none" stroke="#1a93cc" stroke-width="1.6"/></svg><span>Available in 1, 5, 55 and 275-gallon packages</span></li>
    <li class="wide"><svg width="15" height="15" viewBox="0 0 16 16"><circle cx="8" cy="8" r="7" fill="none" stroke="#1a93cc" stroke-width="1.4"/><path d="M4.6 8.2l2.3 2.2 4.4-4.6" fill="none" stroke="#1a93cc" stroke-width="1.6"/></svg><span>Effective on killing germs without drying out your hands</span></li>
  </ul>
  <svg class="nav-arrow nav-prev" width="24" height="34" viewBox="0 0 24 34"><path d="M19 3L5 17l14 14" fill="none" stroke="#666" stroke-width="4"/></svg>
  <svg class="nav-arrow nav-next" width="24" height="34" viewBox="0 0 24 34"><path d="M5 3l14 14L5 31" fill="none" stroke="#666" stroke-width="4"/></svg>
</header>

<div class="product-photo" role="img" aria-label="Photo of a one-gallon Clendora sanitizer jug"></div>

<table class="pricing">
  <colgroup><col style="width:168px"><col style="width:91px"><col style="width:108px"><col style="width:101px"><col style="width:151px"></colgroup>
  <thead><tr><th>Container</th><th>Min Order<br>Qty</th><th class="nosep">Price<br>($ per Gallon)</th><th>Part<br>Number</th><th>Price per<br>Ounce</th></tr></thead>
  <tbody>
    <tr><td>1 Gallon / 4 per case</td><td>48</td><td class="nosep">$27.92</td><td>IP4148</td><td>0.218125</td></tr>
    <tr><td>5 Gallon Pail</td><td>36</td><td class="nosep">$25.86</td><td>IP5400</td><td>0.202031</td></tr>
    <tr><td>55 Gallon Drum</td><td>4</td><td class="nosep">$22.42</td><td>IP5540</td><td>0.175156</td></tr>
    <tr><td>275 Gallon Tote</td><td>1</td><td class="nosep">$20.24</td><td>IP2751</td><td>0.158125</td></tr>
  </tbody>
</table>

<div class="stock"><p>In Stock Ready to Ship</p><p>Call 555-207-3318 for inquiries</p></div>
<a class="doc-link doc-compliance" href="#"><svg width="18" height="18" viewBox="0 0 18 18"><path d="M3 4h8l4 4v7H3z" fill="none" stroke="#1a93cc" stroke-width="1.3"/></svg>Letter of Compliance</a>
<a class="doc-link doc-sds" href="#"><svg width="18" height="18" viewBox="0 0 18 18"><path d="M3 4h8l4 4v7H3z" fill="none" stroke="#1a93cc" stroke-width="1.3"/></svg>Safety Data Sheet</a>

<footer class="footer">© 2020 Company Name | All Rights Reserved</footer>
</body>
</html>
```